VOMRA Pty Ltd Business Card

Looking for a simple yet eye-catching double-sided business card design using my company logo on one side and contact details on the other.

Target Market(s)

Government

Industry/Entity Type

Communication Systems Engineering

Contact Information for Business Card

VOMRA Pty Ltd

Requirements
Nice to have
• Would be great to have a QR code so details can be scanned into contacts

```html
<!DOCTYPE html>
<html lang="en">
<head>
<meta charset="utf-8">
<title>VOMRA Pty Ltd Business Card</title>
<link href="https://fonts.googleapis.com/css2?family=Open+Sans:wght@400;700&display=swap" rel="stylesheet">
<style>
  :root {
    --stage: #222324;
    --slate: #37424a;
    --paper: #ffffff;
    --ink: #37424a;
    --text: #1f2326;
  }
  * { box-sizing: border-box; margin: 0; padding: 0; }
  html, body { width: 1200px; height: 780px; overflow: hidden; background: var(--stage); }
  body { position: relative; font-family: "Open Sans", Arial, sans-serif; }

  .card {
    position: absolute;
    width: 600px; height: 343px;
    border-radius: 22px;
    overflow: hidden;
  }
  .card--back { left: 80px; top: 35px; background: var(--slate); }
  .card--front { left: 520px; top: 400px; background: var(--paper); }

  .brand { position: absolute; display: flex; align-items: center; gap: 16px; }
  .brand__dot { border-radius: 50%; }
  .brand__name { font-weight: 700; letter-spacing: 4px; line-height: 1; }

  .card--back .brand { left: 50%; top: 50%; transform: translate(-50%, -50%); }
  .card--back .brand__dot { width: 34px; height: 34px; background: var(--paper); }
  .card--back .brand__name { font-size: 64px; color: var(--paper); }

  .swoosh { position: absolute; inset: 0; width: 100%; height: 100%; }

  .card--front .brand { left: 34px; top: 40px; }
  .card--front .brand__dot { width: 24px; height: 24px; background: var(--ink); }
  .card--front .brand__name { font-size: 42px; color: var(--ink); }

  .person { position: absolute; right: 30px; top: 26px; text-align: right; }
  .person__name { font-size: 27px; font-weight: 700; color: var(--ink); line-height: 1.1; }
  .person__role { font-size: 13px; color: var(--text); }
  .edge-tab { position: absolute; right: 0; top: 14px; width: 14px; height: 50px; background: var(--slate); }

  .details { position: absolute; left: 34px; top: 148px; color: var(--text); font-size: 14px; line-height: 1.35; }
  .details__address { margin-bottom: 10px; }
  .contact { list-style: none; }
  .contact li { display: flex; align-items: center; gap: 9px; }
  .contact svg { width: 13px; height: 13px; flex: none; }
</style>
</head>
<body>

<section class="card card--back" aria-label="Card back">
  <div class="brand">
    <span class="brand__dot"></span>
    <span class="brand__name">VOMRA</span>
  </div>
</section>

<section class="card card--front" aria-label="Card front">
  <svg class="swoosh" viewBox="0 0 600 343" preserveAspectRatio="none" aria-hidden="true">
    <path d="M0 343 L0 318 C190 312 320 270 410 175 C460 122 530 108 600 116 L600 343 Z" fill="#37424a"/>
    <path d="M0 332 C150 328 300 300 380 232" fill="none" stroke="#ffffff" stroke-width="4"/>
  </svg>

  <div class="edge-tab"></div>
  <div class="person">
    <p class="person__name">Dana Whitlow</p>
    <p class="person__role">Co-Founder</p>
  </div>

  <div class="brand">
    <span class="brand__dot"></span>
    <span class="brand__name">VOMRA</span>
  </div>

  <div class="details">
    <p class="details__address">42-44 Harbour Lane Redfern<br>NSW 2016 Australia</p>
    <ul class="contact">
      <li>
        <svg viewBox="0 0 16 16" aria-hidden="true"><circle cx="8" cy="8" r="8" fill="#37424a"/><path d="M5 4.5l1.5-.5 1 2-1 .8c.5 1 1.2 1.7 2.2 2.2l.8-1 2 1-.5 1.5c-3 0-6-3-6-6z" fill="#fff"/></svg>
        (555) 214-0376
      </li>
      <li>
        <svg viewBox="0 0 16 16" aria-hidden="true"><circle cx="8" cy="8" r="8" fill="#37424a"/><circle cx="8" cy="8" r="4.5" fill="none" stroke="#fff" stroke-width="1"/><path d="M3.5 8h9M8 3.5c-2 2.5-2 6.5 0 9M8 3.5c2 2.5 2 6.5 0 9" fill="none" stroke="#fff" stroke-width="0.8"/></svg>
        www.vomra.com.au
      </li>
      <li>
        <svg viewBox="0 0 16 16" aria-hidden="true"><circle cx="8" cy="8" r="8" fill="#37424a"/><rect x="4" y="5.5" width="8" height="5.5" fill="none" stroke="#fff" stroke-width="1"/><path d="M4 5.5l4 3 4-3" fill="none" stroke="#fff" stroke-width="1"/></svg>
        admin@vomra.com.au
      </li>
    </ul>
  </div>
</section>

</body>
</html>
```